Personal Trainer website design

We are working with a personal trainer to design a website. They offer their primary services: Diet Coaching, In-Person Coaching (workouts), and Remote Coaching.
Some sites we like: https://www.mirabelthorne.com, https://kavialune.com/en-us, https://corvexfit.co.uk
Thank you for taking the time to consider designing a website for us. We are web developers based in Stockton, CA USA. Most of our projects go through the same process. Understanding this process may help you win a project with us. We custom-code all of our websites in-house. We don’t have any requirements as to what tools you use for your design, but ask that you follow these guidelines.
IMAGES:
We ask that if you use any images, or icons in the design, have a link to the asset, so we can purchase the image/icon. Most of the designs we submit do not have the customer’s images on them unless they have some great images. Be creative; show us the feeling that you are trying to portray with your image choices. Use any royalty-free site you choose. We subscribe to Quillon and mostly use their images, but are ok to purchase images outside of Quillon.
FONTS:
We ask that you identify the fonts you’re using in the design. This can be done in a message if you want. We typically use Brivane Fonts and Quillon Fonts.
CONTENT:
We're always open to different content and ideas. Often, we submit designs with stock images so that the client can see our vision. We typically go back and take pictures after the website launch to use their images with our vision. Lorem Ipsum is fine for paragraphs, but we ask that you make the Headers with correct English. We want to be able to show the vision and identify the sections of the website.
INSPIRATION:
We try and add a couple of links in the brief of some websites that we like to help you get started in your design.
REVISIONS:
We do not often ask for revisions of the designs unless we see something in the design that may not appeal to the client. If there are slight changes that we want to make, we simply do that in the development process.
FEEDBACK:
We rarely give feedback on designs during the design process. We are working on many website projects and do not have the time to give feedback. We usually respond if your request is well thought out and asks specific questions, but a note asking “feedback, please” usually goes unanswered.
1 page

```html
<!DOCTYPE html>
<html lang="en">
<head>
<meta charset="utf-8">
<title>Novaform — Personal Training</title>
<link href="https://fonts.googleapis.com/css2?family=Alegreya+Sans:ital,wght@0,500;1,400;1,500;1,700&display=swap" rel="stylesheet">
<style>
  :root {
    --olive: #7f8c12;
    --olive-light: #9aa61e;
    --cream: #f1efd2;
    --ink: #111111;
    --black: #050505;
    --white: #ffffff;
    --grey-line: #5a5a5a;
  }
  * { margin: 0; padding: 0; box-sizing: border-box; }
  html, body { width: 1200px; height: 3465px; overflow: hidden; background: var(--white); }
  body { position: relative; font-family: "Alegreya Sans", sans-serif; font-style: italic; color: var(--ink); }
  .abs { position: absolute; }

  /* header */
  .site-header { position: absolute; left: 0; top: 0; width: 1200px; height: 117px; background: var(--white); }
  .brand { position: absolute; left: 120px; top: 34px; display: flex; align-items: center; gap: 12px;
    font-size: 50px; font-weight: 700; font-style: italic; color: var(--ink); letter-spacing: 1px; }
  .brand-dot { width: 30px; height: 30px; border-radius: 50%; background: var(--olive); }
  .menu-toggle { position: absolute; left: 1025px; top: 38px; }

  /* hero */
  .hero { position: absolute; left: 0; top: 117px; }
  .hero-title { position: absolute; left: 0; width: 1200px; top: 285px; text-align: center;
    font-size: 72px; font-weight: 500;
    background: linear-gradient(180deg, var(--cream) 0%, #c9cc7a 60%, var(--olive-light) 100%);
    -webkit-background-clip: text; background-clip: text; color: transparent; }
  .play-button { position: absolute; left: 573px; top: 404px; }

  /* section text */
  .section-title { position: absolute; font-size: 54px; font-weight: 500; color: var(--olive); line-height: 1.1; }
  .body-copy { position: absolute; font-size: 27px; line-height: 37.7px; }
  .btn { position: absolute; width: 171px; height: 47px; border-radius: 12px; background: var(--olive);
    color: var(--white); font-size: 26px; text-align: center; line-height: 47px; }

  .feature-list { position: absolute; left: 118px; top: 1922px; list-style: none; color: var(--white); font-size: 28px; }
  .feature-list li { position: relative; padding-left: 29px; height: 47px; line-height: 44px; }
  .feature-list li::before { content: ""; position: absolute; left: 2px; top: 20px; width: 9px; height: 9px;
    border-radius: 50%; background: var(--olive-light); }

  /* services */
  .service-label { position: absolute; width: 340px; text-align: center; top: 2812px; font-size: 31px; color: var(--ink); }

  /* footer */
  .footer-text { position: absolute; left: 0; width: 1200px; text-align: center; color: var(--white); }
  .footer-heading { top: 3060px; font-size: 27px; font-weight: 500; }
  .footer-about { top: 3116px; font-size: 15px; line-height: 25px; }
  .footer-phone { top: 3179px; font-size: 16px; }
  .footer-links { top: 3205px; font-size: 14px; }
  .footer-address { top: 3247px; font-size: 15px; }
  .footer-copy { top: 3418px; font-size: 17px; }
  .social { position: absolute; left: 0; top: 3310px; width: 1200px; display: flex; justify-content: center; gap: 28px; list-style: none; }
  .social li { width: 35px; height: 35px; border-radius: 50%; background: var(--white); }
  .footer-rule { position: absolute; left: 0; top: 3385px; width: 1200px; height: 1px; background: var(--grey-line); }
</style>
</head>
<body>

<header class="site-header">
  <div class="brand"><span>NOVAFORM</span><span class="brand-dot"></span></div>
  <svg class="menu-toggle" width="64" height="52" viewBox="0 0 64 52" aria-label="Menu">
    <g stroke="#7f8c12" stroke-width="6" stroke-linecap="round">
      <line x1="3" y1="4" x2="60" y2="4"/>
      <line x1="3" y1="24" x2="48" y2="24"/>
      <line x1="3" y1="44" x2="28" y2="44"/>
    </g>
  </svg>
</header>

<section class="hero">
  <svg width="1200" height="820" viewBox="0 0 1200 820" role="img" aria-label="Photo: athlete lifting dumbbells, seen from behind, on a dark background">
    <defs>
      <radialGradient id="heroGlow" cx="50%" cy="45%" r="60%">
        <stop offset="0" stop-color="#5a4030"/>
        <stop offset="0.45" stop-color="#2a1e18"/>
        <stop offset="1" stop-color="#050505"/>
      </radialGradient>
    </defs>
    <polygon points="0,0 1200,0 1200,656 0,818" fill="url(#heroGlow)"/>
  </svg>
  <h1 class="hero-title">Welcome to Novaform</h1>
  <svg class="play-button" width="56" height="56" viewBox="0 0 56 56" aria-label="Play video">
    <circle cx="28" cy="28" r="25" fill="none" stroke="#fff" stroke-width="3"/>
    <polygon points="22,17 39,28 22,39" fill="none" stroke="#fff" stroke-width="3" stroke-linejoin="round"/>
  </svg>
</section>

<section class="about">
  <h2 class="section-title" style="left:112px; top:1012px;">About Us</h2>
  <p class="body-copy" style="left:112px; top:1100px; width:405px;">Lorem Ipsum is simply dummy text of the printing and typesetting industry. Lorem Ipsum has been the industry's standard dummy text ever since the 1500s, when an unknown printer took a galley of type and scrambled it to make a type specimen book.</p>
  <div class="btn" style="left:112px; top:1437px;">Read More</div>
  <svg class="abs" style="left:540px; top:930px;" width="560" height="590" viewBox="0 0 560 590" role="img" aria-label="Photo: trainer coaching a client doing squats in a gym">
    <defs>
      <linearGradient id="aboutPhoto" x1="0" y1="0" x2="1" y2="1">
        <stop offset="0" stop-color="#6a6c70"/>
        <stop offset="0.55" stop-color="#34353a"/>
        <stop offset="1" stop-color="#1a1a1c"/>
      </linearGradient>
    </defs>
    <circle cx="280" cy="318" r="260" fill="#7f8c12"/>
    <circle cx="280" cy="279" r="266" fill="url(#aboutPhoto)" stroke="#ffffff" stroke-width="4"/>
  </svg>
</section>

<section class="method">
  <svg class="abs" style="left:0; top:1480px;" width="1200" height="845" viewBox="0 0 1200 845" role="img" aria-label="Photo: trainer with clipboard guiding a client on an exercise ball">
    <defs>
      <linearGradient id="methodPhoto" x1="0" y1="0" x2="1" y2="1">
        <stop offset="0" stop-color="#8a7a66"/>
        <stop offset="0.5" stop-color="#b79a78"/>
        <stop offset="1" stop-color="#6f8aa0"/>
      </linearGradient>
    </defs>
    <path d="M0,2 L780,320 L560,822 L0,822 Z" fill="#050505"/>
    <path d="M500,840 C505,420 790,80 1200,27 L1200,840 Z" fill="url(#methodPhoto)"/>
  </svg>
  <h2 class="section-title" style="left:110px; top:1674px;">Lorem Ipsum</h2>
  <p class="body-copy" style="left:112px; top:1757px; width:360px; color:var(--white);">t is a long established fact that a reader will be distracted by the readable content of a page when looking at its layout.</p>
  <ul class="feature-list">
    <li>Contrary to popular belief</li>
    <li>Contrary to popular belief</li>
    <li>Contrary to popular belief</li>
    <li>Contrary to popular belief</li>
  </ul>
  <div class="btn" style="left:112px; top:2183px;">Read More</div>
</section>

<section class="services">
  <h2 class="section-title" style="left:0; width:1200px; text-align:center; top:2382px;">Our Services</h2>
  <svg class="abs" style="left:0; top:2460px;" width="1200" height="345" viewBox="0 0 1200 345" role="img" aria-label="Photos: diet planning, gym workout, remote video coaching">
    <defs>
      <linearGradient id="svcDiet" x1="0" y1="0" x2="1" y2="1"><stop offset="0" stop-color="#3a5a6a"/><stop offset="1" stop-color="#c98a5a"/></linearGradient>
      <linearGradient id="svcGym" x1="0" y1="0" x2="1" y2="1"><stop offset="0" stop-color="#3d3a2e"/><stop offset="1" stop-color="#9a9a92"/></linearGradient>
      <linearGradient id="svcRemote" x1="0" y1="0" x2="1" y2="1"><stop offset="0" stop-color="#d8dcd8"/><stop offset="1" stop-color="#b3a695"/></linearGradient>
    </defs>
    <circle cx="264" cy="196" r="139" fill="#7f8c12"/>
    <circle cx="600" cy="196" r="139" fill="#7f8c12"/>
    <circle cx="935" cy="196" r="139" fill="#7f8c12"/>
    <circle cx="264" cy="166" r="151" fill="url(#svcDiet)" stroke="#ffffff" stroke-width="3"/>
    <circle cx="600" cy="166" r="151" fill="url(#svcGym)" stroke="#ffffff" stroke-width="3"/>
    <circle cx="935" cy="166" r="151" fill="url(#svcRemote)" stroke="#ffffff" stroke-width="3"/>
  </svg>
  <div class="service-label" style="left:94px;">Diet Coaching</div>
  <div class="service-label" style="left:430px;">In-Person Coaching</div>
  <div class="service-label" style="left:765px;">Remote Coaching</div>
</section>

<footer class="site-footer">
  <svg class="abs" style="left:0; top:2884px;" width="1200" height="581" viewBox="0 0 1200 581" role="img" aria-label="Dimmed background photo of an athlete training">
    <defs>
      <linearGradient id="footerPhoto" x1="0" y1="0" x2="1" y2="1">
        <stop offset="0" stop-color="#2a2620"/>
        <stop offset="0.5" stop-color="#15130f"/>
        <stop offset="1" stop-color="#241a1a"/>
      </linearGradient>
    </defs>
    <rect width="1200" height="581" fill="url(#footerPhoto)"/>
    <polygon points="0,0 1200,0 600,140" fill="#ffffff"/>
  </svg>
  <h3 class="footer-text footer-heading">About Us</h3>
  <p class="footer-text footer-about">Lorem Ipsum is simply dummy text of the<br>printing and typesetting industry.</p>
  <p class="footer-text footer-phone">1+555-014-2290</p>
  <p class="footer-text footer-links">Terms of Service | Contact</p>
  <p class="footer-text footer-address">30000,Novaform Lorem Ipsum ,,is simply. 000000</p>
  <ul class="social" aria-label="Social links">
    <li aria-label="Social profile 1"></li>
    <li aria-label="Social profile 2"></li>
    <li aria-label="Social profile 3"></li>
    <li aria-label="Social profile 4"></li>
    <li aria-label="Social profile 5"></li>
  </ul>
  <div class="footer-rule"></div>
  <p class="footer-text footer-copy">Copyright © 2023 Novaform,&nbsp; - All Rights Reserved.</p>
</footer>

</body>
</html>
```